Income Tax Flyer - Updates Needed

Just need to update this flyer design and give it a new look. We would like to keep all the same wording but make it stand out a little more. Our selling point is the "Same Day Tax Advance up to $6,000"

Lending, Small Loans, Tax Services, Title Loans, Personal Loans

```html
<!DOCTYPE html>
<html lang="en">
<head>
<meta charset="UTF-8">
<title>Same Day Tax Advance Flyer</title>
<link rel="stylesheet" href="https://fonts.googleapis.com/css2?family=Montserrat:wght@800;900&family=Bebas+Neue&family=Lexend:wght@400;500;600&display=swap">
<style>
  :root{
    --page-bg:#23263c;
    --red:#c11f27;
    --red-dark:#8e0d12;
    --green:#4a9a5c;
    --green-bright:#2fb84a;
    --green-neon:#00ff2a;
    --green-deep:#1e6b33;
    --ink:#141414;
    --white:#ffffff;
  }
  *{box-sizing:border-box;margin:0;padding:0}
  html,body{width:1200px;height:1200px;overflow:hidden;background:var(--page-bg)}
  .flyer{position:absolute;left:190px;top:20px;width:820px;height:1160px;background:var(--white);overflow:hidden;font-family:"Lexend",sans-serif}
  .hero{position:absolute;left:0;top:0;width:820px;height:697px;background:radial-gradient(ellipse at 50% 55%,#c8202a 0%,#b41a22 45%,#a0141b 100%)}
  .ground{position:absolute;left:0;top:697px;width:820px;height:208px;background:linear-gradient(180deg,var(--green) 0%,#3fa556 60%,var(--green-bright) 100%)}
  .photo{position:absolute;left:96px;top:372px;width:656px;height:403px;border-radius:40px 40px 10px 10px;background:radial-gradient(ellipse at 50% 50%,rgba(230,220,215,.55) 0%,rgba(120,110,120,.35) 55%,rgba(0,0,0,0) 80%)}
  .badge{position:absolute;left:140px;top:40px;width:144px;height:144px;border-radius:50%;background:var(--green);border:6px solid var(--red-dark);display:flex;align-items:center;justify-content:center}
  .badge-text{font-family:"Bebas Neue",sans-serif;color:var(--white);font-size:46px;line-height:.85;text-align:center;transform:rotate(-14deg);-webkit-text-stroke:1px var(--red-dark)}
  .headline{position:absolute;font-family:"Montserrat",sans-serif;font-weight:900;color:var(--white);-webkit-text-stroke:5px var(--red-dark);paint-order:stroke fill;line-height:1;letter-spacing:1px}
  .headline-tax{left:285px;top:38px;font-size:146px;letter-spacing:6px}
  .headline-advance{left:130px;top:168px;font-size:110px;letter-spacing:-1px}
  .up-to{position:absolute;left:134px;top:279px;width:68px;height:23px;background:#000;color:var(--white);font-size:16px;font-weight:600;display:flex;align-items:center;justify-content:center}
  .amount{position:absolute;left:130px;top:262px;font-family:"Montserrat",sans-serif;font-weight:800;font-size:162px;line-height:1;letter-spacing:-2px;background:linear-gradient(180deg,var(--green-neon) 0%,var(--green-neon) 42%,#2b9a45 60%,#3aa552 100%);-webkit-background-clip:text;background-clip:text;color:transparent;-webkit-text-stroke:3px var(--red-dark)}
  .amount .currency{font-size:96px;vertical-align:18px}
  .tagline{position:absolute;left:0;top:782px;width:820px;text-align:center;font-family:"Bebas Neue",sans-serif;font-size:38px;color:var(--white);letter-spacing:.5px;-webkit-text-stroke:4px var(--green-deep);paint-order:stroke fill}
  .feature{position:absolute;top:828px;height:77px;display:flex;align-items:flex-start}
  .feature-tab{width:68px;height:77px;background:var(--red);border:3px solid var(--red-dark);border-bottom:none;border-radius:34px 34px 0 0;display:flex;align-items:center;justify-content:center}
  .feature-text{margin-left:10px;margin-top:14px;font-size:21px;line-height:1.28;color:var(--ink)}
  .contact-bar{position:absolute;left:0;top:905px;width:820px;height:64px;background:#000;display:flex;align-items:center;padding-left:64px;font-size:32px;font-weight:500;color:var(--white);letter-spacing:1px}
  .contact-phone{color:var(--red);font-weight:600;margin-left:22px}
  .brand{position:absolute;left:59px;top:1020px;display:flex;align-items:center;gap:12px}
  .brand-mark{width:28px;height:28px;border-radius:50%;background:var(--green-deep)}
  .brand-name{font-size:30px;font-weight:500;color:var(--green-deep);line-height:1.15}
  .location{position:absolute;left:349px;top:1011px;width:421px;height:36px;background:var(--red);border-radius:0 18px 18px 0;color:var(--white);font-size:25px;font-weight:500;display:flex;align-items:center;padding-left:16px}
  .pin{position:absolute;left:349px;top:1066px;width:49px;height:48px;border-radius:24px 24px 0 0;background:linear-gradient(180deg,var(--green-neon),var(--green))}
  .address{position:absolute;left:417px;top:1064px;font-size:23px;font-weight:500;line-height:1.28;color:var(--ink)}
</style>
</head>
<body>
<main class="flyer">
  <div class="hero"></div>
  <div class="ground"></div>
  <div class="photo" role="img" aria-label="Smiling couple sitting cross-legged holding cash and a laptop, with banknotes flying around"></div>

  <div class="badge"><span class="badge-text">SAME<br>DAY</span></div>
  <div class="headline headline-tax">TAX</div>
  <div class="headline headline-advance">ADVANCE</div>
  <div class="up-to">UP TO</div>
  <div class="amount"><span class="currency">$</span>6,000</div>

  <p class="tagline">FILE YOUR TAXES &amp; APPLY FOR AN EASY ADVANCE!</p>

  <div class="feature" style="left:59px">
    <div class="feature-tab">
      <svg width="40" height="40" viewBox="0 0 40 40" fill="none" stroke="#fff" stroke-width="2"><circle cx="18" cy="22" r="13"/><path d="M18 14v8l5 4M15 6h6M18 6v3"/><circle cx="30" cy="31" r="6" fill="var(--red)"/><path d="M30 28v6"/></svg>
    </div>
    <p class="feature-text">Available in<br>24 Hours or Less</p>
  </div>
  <div class="feature" style="left:334px">
    <div class="feature-tab">
      <svg width="40" height="40" viewBox="0 0 40 40" fill="none" stroke="#fff" stroke-width="2"><circle cx="16" cy="15" r="10"/><path d="M16 9v12M19 11h-4a2 2 0 0 0 0 4h2a2 2 0 0 1 0 4h-4"/><path d="M22 24l3 10h9l-2-8-6-2"/></svg>
    </div>
    <p class="feature-text">Choose Your<br>Loan Amount</p>
  </div>
  <div class="feature" style="left:575px">
    <div class="feature-tab">
      <svg width="40" height="40" viewBox="0 0 40 40" fill="none" stroke="#fff" stroke-width="2"><rect x="12" y="7" width="24" height="12" rx="2"/><circle cx="24" cy="13" r="3"/><path d="M3 10h6M5 14h5M4 26l8-3h10l-2 4h-8M4 33l6-2h14l10-8"/></svg>
    </div>
    <p class="feature-text">Quick<br>and Easy</p>
  </div>

  <div class="contact-bar">CONTACT US TODAY!<span class="contact-phone">(555) 210-4730</span></div>

  <div class="brand"><span class="brand-mark"></span><span class="brand-name">Keystone<br>Lending Group</span></div>

  <div class="location">AUSTIN – MERIDIAN</div>
  <div class="pin">
    <svg width="49" height="48" viewBox="0 0 49 48" fill="none" stroke="#1a3d24" stroke-width="2"><path d="M24.5 36s-9-9-9-16a9 9 0 0 1 18 0c0 7-9 16-9 16z"/><circle cx="24.5" cy="20" r="3.5"/><ellipse cx="24.5" cy="38" rx="9" ry="3"/></svg>
  </div>
  <p class="address">4120-2 Meridian Ave<br>Austin, Texas 78745</p>
</main>
</body>
</html>
```